Business Card Design for a Personal Trainer

I need a business card design for my job as a personal trainer. It should have a unique, modern and exclusive design. On the front there should be only my logo with my name and my job. 0162/3819204 Tobias Lendhart Wiesengrundweg 14 80417 Munich Germany The most important contact information is the web adress. it can be bigger than the rest, but its not necessary. The card should be 8,5cmx5,5cm big. Font: Roboto. Colors: black, white, gray, 56c1ff.

```html
<!DOCTYPE html>
<html lang="de">
<head>
<meta charset="utf-8">
<title>Tobias Lendhart – Visitenkarte</title>
<link rel="stylesheet" href="https://fonts.googleapis.com/css2?family=Roboto:wght@300;400;500;700&display=swap">
<style>
  :root {
    --page: #f2f2f2;
    --white: #ffffff;
    --black: #000000;
    --ink: #1e1e1e;
    --dark-card: #2b2b2b;
    --frame: #3a3a3a;
    --grey-step: #6a6a6a;
    --faint: #f1f1f1;
    --muted: #4a4a4a;
  }
  * { box-sizing: border-box; margin: 0; padding: 0; }
  html, body { width: 1136px; height: 1200px; overflow: hidden; }
  body {
    background: var(--page);
    font-family: "Roboto", sans-serif;
    display: flex;
    flex-direction: column;
    align-items: center;
    justify-content: center;
    gap: 60px;
  }
  .card {
    position: relative;
    width: 800px;
    height: 518px;
    overflow: hidden;
    box-shadow: 0 6px 18px rgba(0,0,0,0.28);
  }

  /* Contact side */
  .card--contact { background: var(--white); }
  .watermark-name {
    position: absolute;
    left: 24px; top: 96px;
    width: 460px;
    font-size: 40px;
    font-weight: 700;
    color: var(--faint);
    letter-spacing: 1px;
    line-height: 1;
    white-space: nowrap;
  }
  .grey-step {
    position: absolute;
    left: 0; top: 178px;
    width: 394px; height: 14px;
    background: var(--grey-step);
  }
  .black-band {
    position: absolute;
    left: 0; top: 192px;
    width: 100%; height: 43px;
    background: var(--black);
  }
  .portrait-frame {
    position: absolute;
    left: 514px; top: 43px;
    width: 246px; height: 246px;
    border: 5px solid var(--frame);
    background: var(--white);
    padding: 9px;
  }
  .portrait {
    width: 100%; height: 100%;
    background: linear-gradient(180deg, #e9e9e9 0%, #bdbdbd 55%, #4a4a4a 100%);
  }
  .identity {
    position: absolute;
    left: 514px; top: 316px;
    width: 246px;
    text-align: center;
  }
  .identity__name {
    font-size: 26px;
    font-weight: 700;
    color: var(--ink);
    letter-spacing: 1px;
  }
  .identity__role {
    font-size: 20px;
    font-weight: 400;
    color: var(--muted);
    letter-spacing: 1px;
    margin-top: 2px;
  }
  .contact-list {
    position: absolute;
    left: 44px; top: 256px;
    list-style: none;
  }
  .contact-list li {
    display: flex;
    align-items: flex-start;
    gap: 18px;
    font-size: 25px;
    font-weight: 300;
    color: var(--ink);
    letter-spacing: 1.5px;
    line-height: 33px;
    margin-bottom: 13px;
    white-space: nowrap;
  }
  .contact-list svg {
    width: 20px; height: 20px;
    flex: none;
    margin-top: 7px;
    fill: var(--ink);
  }

  /* Logo side */
  .card--brand {
    background: var(--dark-card);
    color: var(--white);
    display: flex;
    flex-direction: column;
    align-items: center;
    justify-content: center;
  }
  .brand-mark {
    width: 58px; height: 58px;
    background: var(--white);
    margin-bottom: 34px;
  }
  .brand-name {
    font-size: 50px;
    font-weight: 400;
    letter-spacing: 1px;
    line-height: 1;
  }
  .brand-role {
    display: flex;
    align-items: center;
    gap: 12px;
    margin-top: 12px;
    font-size: 23px;
    font-weight: 400;
    letter-spacing: 5px;
  }
  .brand-role::before,
  .brand-role::after {
    content: "";
    width: 86px;
    height: 2px;
    background: var(--white);
  }
</style>
</head>
<body>

  <section class="card card--contact" aria-label="Kontaktseite">
    <div class="watermark-name" aria-hidden="true">TOBIAS LENDHART</div>
    <div class="grey-step"></div>
    <div class="black-band"></div>

    <div class="portrait-frame">
      <div class="portrait" role="img" aria-label="Schwarz-Weiß-Porträt des Trainers mit verschränkten Armen"></div>
    </div>

    <div class="identity">
      <p class="identity__name">Tobias Lendhart</p>
      <p class="identity__role">Personal Trainer</p>
    </div>

    <ul class="contact-list">
      <li>
        <svg viewBox="0 0 24 24" aria-hidden="true"><path d="M6.6 10.8a15.2 15.2 0 0 0 6.6 6.6l2.2-2.2a1 1 0 0 1 1-.25 11.4 11.4 0 0 0 3.6.57 1 1 0 0 1 1 1V20a1 1 0 0 1-1 1A17 17 0 0 1 3 4a1 1 0 0 1 1-1h3.5a1 1 0 0 1 1 1c0 1.25.2 2.45.57 3.57a1 1 0 0 1-.25 1z"/></svg>
        <span>0162/3819204</span>
      </li>
      <li>
        <svg viewBox="0 0 24 24" aria-hidden="true"><path d="M2 6.5 12 13l10-6.5V5H2zM2 8.8V19h20V8.8l-10 6.5z"/></svg>
        <span>t.lendhart@tl-mailpost.de</span>
      </li>
      <li>
        <svg viewBox="0 0 24 24" aria-hidden="true"><path d="M12 2a10 10 0 1 0 0 20 10 10 0 0 0 0-20zm6.9 6h-2.9a15.7 15.7 0 0 0-1.4-3.6A8 8 0 0 1 18.9 8zM12 4c.8 1.2 1.5 2.5 1.9 4h-3.8c.4-1.5 1.1-2.8 1.9-4zM4.3 14a8.2 8.2 0 0 1 0-4h3.4a16.5 16.5 0 0 0 0 4zm.8 2H8c.3 1.3.8 2.5 1.4 3.6A8 8 0 0 1 5.1 16zM8 8H5.1a8 8 0 0 1 4.3-3.6C8.8 5.5 8.4 6.7 8 8zm4 12c-.8-1.2-1.5-2.5-1.9-4h3.8c-.4 1.5-1.1 2.8-1.9 4zm2.3-6H9.7a14.7 14.7 0 0 1 0-4h4.6a14.7 14.7 0 0 1 0 4zm.3 5.6c.6-1.1 1.1-2.3 1.4-3.6h2.9a8 8 0 0 1-4.3 3.6zm1.7-5.6a16.5 16.5 0 0 0 0-4h3.4a8.2 8.2 0 0 1 0 4z"/></svg>
        <span>www.tobiaslendhart.de</span>
      </li>
      <li>
        <svg viewBox="0 0 24 24" aria-hidden="true"><path d="M12 2a7 7 0 0 0-7 7c0 5.2 7 13 7 13s7-7.8 7-13a7 7 0 0 0-7-7zm0 9.5A2.5 2.5 0 1 1 12 6.5a2.5 2.5 0 0 1 0 5z"/></svg>
        <span>Wiesengrundweg 14<br>80417 München</span>
      </li>
    </ul>
  </section>

  <section class="card card--brand" aria-label="Logoseite">
    <div class="brand-mark" aria-hidden="true"></div>
    <h1 class="brand-name">TOBIAS LENDHART</h1>
    <p class="brand-role">PERSONAL TRAINER</p>
  </section>

</body>
</html>
```